Flyer design 3-part folding flyer

A template for a 3-fold print flyer is to be created.

The flyer should be professional and customer-oriented as an advertising flyer that leads to the purchase of the consulting service.

The structure is an example and can be customized.
The topics are as follows:
Create a 3-part folded flyer:
🧠 Flyer design: KORV Business Partner GmbH
🎨 Color scheme
Orange: Energy, innovation, attention
White: Clarity, trust
Anthracite: seriousness, stability

πŸ”Ά Front (Panel 1 – Title Page)
Title: From Chaos to Clarity – AI in Your Supply Chain
Image idea: An entrepreneur with a desperate look in front of a mountain of documents and storage chaos (horror of horrors) – next to it a signpost towards the β€œBeach of Bliss” with the logo of KORV Business Partner GmbH.
Slogan: KORV gets your supply chain on track – with artificial intelligence.

πŸ”Ά Inside (Panel 2 – Problem & Solution)
Headline: The challenges of modern supply chains
Key points (problem):
Overcrowded warehouses & capital tie-up
Unclear demand planning
Supply bottlenecks & production stoppages
Intransparent material flow
Errors that are detected too late
Headline Solution: Our AI solutions – your competitive advantages
Key points (solution):
βœ… Inventory reduction through intelligent forecasts
βœ… Optimized planning with real-time data
βœ… Delivery security through smart algorithms
βœ… Material flow optimization with AI
βœ… Real-time error detection and resolution

πŸ”Ά Back (Panel 3 – Call to Action & Contact)
Headline: Your path to the beach of bliss begins here.
Text: Say goodbye to the horror of horror in your supply chain.
KORV Business Partner GmbH: Experience meets AI – we transform your supply chain from chaos to success. Fast. Precise. Powerful in implementation. πŸš€

Call to Action: πŸ“ž Get a non-binding consultation now +49 162 47193305 🌐 www.korv-beratung.de βœ‰οΈ jonas.hellwig@korv-beratung.de πŸ“ Location: KORV Business Partner GmbH, Lindenwerder Steig 8, D-96472 Kestelbach

Logo & Design: KORV logo positioned at the bottom right, with an orange, white, and anthracite frame and clear typography.

------------------------
If you have any questions or concerns, please contact me.

```html
<!DOCTYPE html>
<html lang="en">
<head>
<meta charset="utf-8">
<title>KORV Business Partner – Tri-fold Flyer</title>
<link href="https://fonts.googleapis.com/css2?family=Arimo:wght@400;700&display=swap" rel="stylesheet">
<style>
  :root{
    --orange:#eba13e;
    --orange-deep:#e8702e;
    --anthracite:#3b4a4a;
    --ink:#2e3333;
    --white:#ffffff;
    --paper-bg:#ffffff;
    --fold:#c9c9c9;
  }
  *{margin:0;padding:0;box-sizing:border-box}
  html,body{width:1189px;height:1200px;overflow:hidden;background:var(--paper-bg);font-family:"Arimo",Arial,sans-serif;color:var(--ink)}
  .sheet{position:absolute;left:204px;width:780px;height:545px;border:1px solid #bdbdbd;background:var(--white);overflow:hidden}
  .sheet--outside{top:35px}
  .sheet--inside{top:620px}
  .sheet__shapes{position:absolute;inset:0;width:780px;height:545px}
  .panel{position:absolute;top:0;width:260px;height:545px}
  .panel--1{left:0}
  .panel--2{left:260px;border-left:1px solid var(--fold)}
  .panel--3{left:520px;border-left:1px solid var(--fold)}
  .headline{position:absolute;left:20px;font-size:19px;font-weight:700;line-height:1.25;white-space:nowrap}
  .headline--dark{color:var(--anthracite)}
  .headline--orange{color:var(--orange)}
  .headline--white{color:var(--white)}
  .intro{position:absolute;left:16px;right:16px;top:138px;text-align:center;font-size:12px;line-height:1.35}
  .intro p{margin-bottom:4px}
  .intro strong{font-weight:700}
  .illustration{position:absolute;left:58px;top:268px;width:142px;height:100px;border-radius:6px;background:linear-gradient(135deg,#f0c79a,#5a6a8a 55%,#e9e1dc)}
  .contacts{position:absolute;left:22px;top:384px;right:10px;font-size:10px;line-height:1.3}
  .contact{display:flex;align-items:flex-start;gap:6px;margin-bottom:10px}
  .contact svg{flex:0 0 14px;width:14px;height:14px;margin-top:1px}
  .contact__phone{font-size:13px;font-weight:700}
  .contact__note{font-size:9px}
  .logo{position:absolute;left:50%;transform:translateX(-50%);bottom:16px;text-align:center;width:136px}
  .logo__row{display:flex;align-items:center;justify-content:center;gap:8px}
  .logo__mark{width:22px;height:22px;background:var(--orange)}
  .logo__name{font-size:34px;font-weight:400;color:var(--anthracite);letter-spacing:1px;line-height:1}
  .logo__sub{margin-top:4px;border-top:1px solid var(--anthracite);padding-top:3px;font-size:8px;letter-spacing:.5px;color:var(--anthracite);text-align:right}
  .bubble{position:absolute;left:47px;top:349px;width:167px;height:89px;background:var(--orange);color:var(--white);font-size:13px;font-weight:700;text-align:center;line-height:1.3;display:flex;align-items:center;justify-content:center;padding:8px 14px}
  .list{position:absolute;left:18px;top:172px;list-style:none;font-size:13px;line-height:1.3}
  .list--problems li{margin-bottom:9px;padding-left:10px;position:relative}
  .list--problems li::before{content:"";position:absolute;left:0;top:7px;width:4px;height:4px;border-radius:50%;background:var(--orange)}
  .list--solutions li{margin-bottom:9px;padding-left:16px;position:relative;font-weight:700}
  .list--solutions li::before{content:"";position:absolute;left:1px;top:3px;width:5px;height:9px;border:solid var(--orange);border-width:0 2px 2px 0;transform:rotate(40deg)}
</style>
</head>
<body>

<section class="sheet sheet--outside">
  <svg class="sheet__shapes" viewBox="0 0 780 545">
    <polygon points="0,0 260,0 260,92 0,128" fill="var(--orange)"/>
    <polygon points="520,0 780,0 780,83 520,114" fill="var(--orange)"/>
    <g role="img" aria-label="Photo of a stressed businessman surrounded by towering stacks of paperwork">
      <defs>
        <linearGradient id="heroTone" x1="0" y1="0" x2="0" y2="1">
          <stop offset="0" stop-color="#e8e2da"/>
          <stop offset=".55" stop-color="#8a8f9a"/>
          <stop offset="1" stop-color="#3e4a60"/>
        </linearGradient>
      </defs>
      <polygon points="520,114 780,83 780,419 520,419" fill="url(#heroTone)"/>
    </g>
    <polygon points="118,438 142,438 130,455" fill="var(--orange)" transform="translate(520,0)"/>
  </svg>

  <div class="panel panel--1">
    <h2 class="headline headline--dark" style="top:28px">Your path to the beach<br>of bliss begins here.</h2>
    <div class="intro">
      <p><strong>Say goodbye to the horror of<br>horror in your supply chain.</strong></p>
      <p>KORV Business Partner GmbH:<br><strong>Experience meets AI</strong></p>
      <p>we transform your supply chain from<br>chaos to success. Fast. Precise.<br>Powerful in implementation</p>
    </div>
    <div class="illustration" role="img" aria-label="Illustration of two consultants shaking hands with an AI robot"></div>
    <div class="contacts">
      <div class="contact">
        <svg viewBox="0 0 14 14" fill="none" stroke="var(--orange)" stroke-width="1.2"><rect x="3" y="1" width="8" height="12"/><line x1="5" y1="4" x2="9" y2="4"/><line x1="5" y1="7" x2="9" y2="7"/><line x1="5" y1="10" x2="9" y2="10"/></svg>
        <div><div class="contact__note">Get a non-binding consultation now</div><div class="contact__phone">+49 162 47193305</div></div>
      </div>
      <div class="contact">
        <svg viewBox="0 0 14 14" fill="none" stroke="var(--orange)" stroke-width="1.2"><circle cx="7" cy="7" r="5.5"/><ellipse cx="7" cy="7" rx="2.5" ry="5.5"/><line x1="1.5" y1="7" x2="12.5" y2="7"/></svg>
        <div>www.korv-beratung.de</div>
      </div>
      <div class="contact">
        <svg viewBox="0 0 14 14" fill="none" stroke="var(--orange)" stroke-width="1.2"><rect x="1" y="3" width="12" height="8"/><polyline points="1,3 7,8 13,3"/></svg>
        <div>jonas.hellwig@korv-beratung.de</div>
      </div>
      <div class="contact">
        <svg viewBox="0 0 14 14" fill="none" stroke="var(--orange)" stroke-width="1.2"><path d="M7 13 C3 8 2.5 6.5 2.5 5 A4.5 4.5 0 0 1 11.5 5 C11.5 6.5 11 8 7 13 Z"/><circle cx="7" cy="5" r="1.6"/></svg>
        <div>KORV Business Partner GmbH,<br>Lindenwerder Steig 8,<br>D-96472 Kestelbach</div>
      </div>
    </div>
  </div>

  <div class="panel panel--2">
    <div class="logo">
      <div class="logo__row"><span class="logo__mark"></span><span class="logo__name">KORV</span></div>
      <div class="logo__sub">BUSINESS PARTNER</div>
    </div>
  </div>

  <div class="panel panel--3">
    <h1 class="headline headline--dark" style="top:22px">From Chaos to Clarity –<br>AI in Your Supply Chain</h1>
    <p class="bubble">KORV gets your supply chain on track – with artificial intelligence.</p>
    <div class="logo">
      <div class="logo__row"><span class="logo__mark"></span><span class="logo__name">KORV</span></div>
      <div class="logo__sub">BUSINESS PARTNER</div>
    </div>
  </div>
</section>

<section class="sheet sheet--inside">
  <svg class="sheet__shapes" viewBox="0 0 780 545">
    <defs>
      <linearGradient id="techTone" x1="0" y1="1" x2="1" y2="0">
        <stop offset="0" stop-color="var(--orange-deep)"/>
        <stop offset=".6" stop-color="#f0913a"/>
        <stop offset="1" stop-color="#f6c45a"/>
      </linearGradient>
    </defs>
    <polygon points="0,0 260,0 260,93 0,128" fill="var(--anthracite)"/>
    <polygon points="260,0 780,0 780,65 260,137" fill="var(--orange)"/>
    <polygon points="0,405 780,298 780,545 0,545" fill="url(#techTone)" role="img" aria-label="Abstract orange technology graphic with glowing circuits and rings"/>
  </svg>

  <div class="panel panel--1">
    <h2 class="headline headline--orange" style="top:28px">The challenges of<br>modern supply chains</h2>
    <ul class="list list--problems">
      <li>Overcrowded warehouses<br>&amp; capital tie-up</li>
      <li>Unclear demand planning</li>
      <li>Supply bottlenecks &amp; production</li>
      <li>stoppages</li>
      <li>Intransparent material flow</li>
      <li>Errors that are detected too late</li>
    </ul>
  </div>

  <div class="panel panel--2" style="z-index:2">
    <h2 class="headline headline--white" style="top:28px">Our AI solutions –<br>your competitive advantages</h2>
    <ul class="list list--solutions">
      <li>Inventory reduction through<br>intelligent forecasts</li>
      <li>Optimized planning with<br>real-time data</li>
      <li>Delivery security through<br>smart algorithms</li>
    </ul>
  </div>

  <div class="panel panel--3">
    <ul class="list list--solutions">
      <li>Material flow optimization<br>with AI</li>
      <li>Real-time error detection<br>and resolution</li>
    </ul>
  </div>
</section>

</body>
</html>
```